Tall ridge firewood

It a new firewood outlet in Jindabyne nsw that will only sell top hardwood firewood (ironbark , red gum, grey gum, an box mix. I would like to see a web page the we can do order online payment for delivery. It will all so need to have photos of the firewood. I all so have logo for tall ridge firewood
Must have a modem look but easy to use I would like to see a black back ground of some sort.

Here are some other firewood web pages for ideas and firewood info
http://www.example-logpile.com.au
http://www.example-stackwood.com.au
http://www.example-splitlog.com.au
http://www.example-kendaltimber.com.au/firewood

Industry/Entity Type

Firewood

```html
<!DOCTYPE html>
<html lang="en">
<head>
<meta charset="utf-8">
<title>Tall Ridge Firewood</title>
<link rel="stylesheet" href="https://fonts.googleapis.com/css2?family=Arimo:wght@400;700&family=Roboto+Condensed:wght@400;700&display=swap">
<style>
:root{
  --blue:#1a6fbf;
  --blue-dark:#155fa6;
  --ink:#222;
  --text:#666;
  --rule:#e2e2e2;
  --black:#111;
  --white:#fff;
  --grey-btn:#e6e6e6;
}
*{box-sizing:border-box;margin:0;padding:0}
html,body{width:966px;height:1200px;overflow:hidden;background:var(--white)}
body{font-family:Arimo,Arial,sans-serif;color:var(--ink)}
.canvas{position:relative;width:966px;height:1200px;overflow:hidden}
.abs{position:absolute}
.top-bar{left:0;top:0;width:966px;height:3px;background:var(--black)}

/* header */
.brand{left:130px;top:30px;display:flex;align-items:center;gap:10px}
.brand-mark{width:54px;height:54px;border-radius:50%;background:var(--blue)}
.brand-name{font-family:'Roboto Condensed',sans-serif;font-weight:700;font-size:19px;color:var(--blue);letter-spacing:.2px}
.contact{top:22px;font-size:9px;color:#444;white-space:nowrap}
.contact b{font-weight:400;color:var(--blue);font-size:10px}
.search{left:540px;top:62px;width:190px;height:19px;border:1px solid #d6d6d6;font-size:9px;color:#999;padding:4px 6px}
.search-btn{left:710px;top:62px;width:20px;height:19px;background:var(--blue)}
.order-btn{left:752px;top:62px;width:84px;height:19px;background:var(--black);border-radius:2px;color:var(--white);font-size:9px;font-weight:700;text-align:center;line-height:19px}
.nav{top:100px;height:40px;display:flex;left:370px;font-size:9px;color:#333}
.nav a{display:block;padding:0 13px;line-height:40px;text-decoration:none;color:inherit}
.nav a.active{background:#eef0f3;color:var(--blue);position:relative}
.nav a.active::after{content:"";position:absolute;left:50%;bottom:0;margin-left:-4px;border:4px solid transparent;border-bottom-color:var(--blue)}
.header-rule{left:0;top:139px;width:966px;height:3px;background:var(--blue)}

/* hero */
.hero{left:0;top:142px;width:966px;height:354px;background:radial-gradient(ellipse at 45% 40%,#e0541a 0%,#a8300e 30%,#3a0f05 65%,#0b0302 100%)}
.arrow{top:301px;width:38px;height:38px;border-radius:50%;background:#8a8a8a}
.caption{left:342px;top:425px;width:282px;height:30px;background:var(--white);font-family:Arimo,sans-serif;font-size:18px;text-align:center;line-height:30px;color:var(--ink)}
.caption span{color:var(--blue)}
.caption::after{content:"";position:absolute;left:50%;bottom:-7px;margin-left:-7px;border:7px solid transparent;border-bottom:0;border-top-color:var(--white)}

/* products */
.product{top:522px;width:180px;text-align:center}
.product-photo{width:122px;height:122px;margin:0 auto;border-radius:50%;border:3px solid #d0d0d0;box-shadow:0 6px 6px -4px rgba(0,0,0,.35)}
.product-photo.featured{border-color:var(--blue)}
.product-name{margin-top:12px;font-family:'Roboto Condensed',sans-serif;font-size:12px;color:var(--ink)}
.product-price{margin-top:2px;font-size:9px;color:#333}
.product-price b{font-size:13px;color:var(--blue);margin-left:3px}
.btn{display:inline-block;height:21px;line-height:21px;padding:0 14px;border-radius:3px;font-size:9px;font-weight:700}
.btn-dark{background:linear-gradient(#3a3a3a,#111);color:var(--white)}
.btn-light{background:linear-gradient(#f4f4f4,#d8d8d8);color:#333;border:1px solid #ccc}
.product .btn{margin-top:10px;width:56px;padding:0}
.vdiv{width:1px;background:var(--rule)}
.view-rule{left:130px;top:762px;width:706px;height:1px;background:var(--rule)}
.view-all{left:409px;top:750px;width:147px;height:25px;background:var(--blue);border-radius:2px;color:var(--white);font-size:11px;text-align:center;line-height:25px}

/* info columns */
.col-heading{top:808px;font-family:'Roboto Condensed',sans-serif;font-size:18px;color:var(--blue)}
.col-text{font-size:9px;line-height:11px;color:var(--text)}
.list-item{display:flex;gap:10px;margin-bottom:13px}
.tick{width:10px;flex:none;margin-top:1px}
.num{font-family:'Roboto Condensed',sans-serif;font-weight:700;font-size:16px;color:var(--ink);width:28px;flex:none;line-height:18px}

/* footer */
.footer{left:0;top:1022px;width:966px;height:148px;background:var(--blue)}
.f-head{font-size:9px;font-weight:700;color:var(--white)}
.f-links{list-style:none;font-size:9px;color:var(--white);line-height:12.8px}
.f-links li::before{content:"»";margin-right:5px}
.fdiv{top:1040px;height:104px;width:1px;background:#3a86cc}
.card{width:28px;height:17px;border-radius:2px;background:var(--white)}
.social{width:22px;height:22px;border-radius:2px}
.copyright{left:0;top:1170px;width:966px;height:30px;background:var(--black);color:var(--white);font-size:9px;text-align:center;line-height:30px}
</style>
</head>
<body>
<div class="canvas">
  <div class="abs top-bar"></div>

  <header>
    <div class="abs brand">
      <div class="brand-mark"></div>
      <div class="brand-name">TALL RIDGE FIREWOOD</div>
    </div>
    <div class="abs contact" style="left:413px">CALL US - <b>0412 555 019</b></div>
    <div class="abs contact" style="left:549px">MAIL US - <b>info@tallridgefirewood.com</b></div>
    <div class="abs contact" style="left:749px">MY CART - <b>0</b> ITEM (S)</div>
    <div class="abs search">Find Firewood Products ..</div>
    <div class="abs search-btn">
      <svg width="20" height="19" viewBox="0 0 20 19"><circle cx="9" cy="8.5" r="4" fill="none" stroke="#fff" stroke-width="2"/><line x1="12" y1="11.5" x2="15" y2="14.5" stroke="#fff" stroke-width="2.2" stroke-linecap="round"/></svg>
    </div>
    <div class="abs order-btn">ORDER ONLINE</div>
    <nav class="abs nav">
      <a class="active">HOME</a><a>ABOUT US</a><a>PRODUCTS</a><a>ACCESSORIES</a><a>DELIVERY</a><a>FAQ`S</a><a style="padding-right:0">CONTACT US</a>
    </nav>
    <div class="abs header-rule"></div>
  </header>

  <section>
    <div class="abs hero" role="img" aria-label="Close-up of glowing hardwood logs burning in a fire"></div>
    <div class="abs arrow" style="left:46px"><svg width="38" height="38"><polyline points="22,10 15,19 22,28" fill="none" stroke="#333" stroke-width="1.5"/></svg></div>
    <div class="abs arrow" style="left:882px"><svg width="38" height="38"><polyline points="16,10 23,19 16,28" fill="none" stroke="#333" stroke-width="1.5"/></svg></div>
    <div class="abs caption"><span>TOP</span> HARDWOOD <span>FIREWOOD</span></div>
  </section>

  <section>
    <div class="abs product" style="left:101px">
      <div class="product-photo featured" role="img" aria-label="Split ironbark log" style="background:radial-gradient(circle at 45% 50%,#b86a32,#5a2e14 60%,#1c0e06)"></div>
      <div class="product-name">IRONBARK</div>
      <div class="product-price">ONLY &nbsp;- <b>$12.30</b></div>
      <span class="btn btn-dark">MORE</span>
    </div>
    <div class="abs vdiv" style="left:289px;top:522px;height:198px"></div>
    <div class="abs product" style="left:296px">
      <div class="product-photo" role="img" aria-label="Pile of red gum firewood" style="background:radial-gradient(circle,#b5644a,#7a3a28 60%,#4a2216)"></div>
      <div class="product-name">RED GUM</div>
      <div class="product-price">ONLY &nbsp;- <b>$15.30</b></div>
      <span class="btn btn-light">MORE</span>
    </div>
    <div class="abs vdiv" style="left:484px;top:522px;height:198px"></div>
    <div class="abs product" style="left:490px">
      <div class="product-photo" role="img" aria-label="Stack of grey gum logs" style="background:radial-gradient(circle,#9a9a9c,#6c6d70 60%,#3f4044)"></div>
      <div class="product-name">GREY GUM</div>
      <div class="product-price">ONLY &nbsp;- <b>$12.30</b></div>
      <span class="btn btn-light">MORE</span>
    </div>
    <div class="abs vdiv" style="left:675px;top:522px;height:198px"></div>
    <div class="abs product" style="left:684px">
      <div class="product-photo" role="img" aria-label="Mixed firewood burning in a fireplace" style="background:radial-gradient(circle at 50% 45%,#f0a030,#8a3a10 35%,#2a1a12 70%)"></div>
      <div class="product-name">BOX MIX</div>
      <div class="product-price">ONLY &nbsp;- <b>$12.30</b></div>
      <span class="btn btn-light">MORE</span>
    </div>
    <div class="abs view-rule"></div>
    <div class="abs view-all">VIEW ALL OUR PRODUCTS</div>
  </section>

  <section>
    <h2 class="abs col-heading" style="left:130px">WELCOME TO OUR SITE</h2>
    <div class="abs col-text" style="left:130px;top:846px;width:180px">
      <p>Lorem ipsum dolor sit amet, consectetur adipisicing elit, sed do eiusmod tempor incididunt ut labore et dolore magna aliqua. Ut enim ad minim veniam, quis nostrud exercitation ullamco.</p>
      <p style="margin-top:11px">Duis aute irure dolor in reprehenderit in voluptate velit esse cillum dolore eu fugiat nulla pariatur ...</p>
    </div>
    <span class="abs btn btn-dark" style="left:130px;top:962px;height:19px;line-height:19px;padding:0 11px">READ MORE</span>
    <div class="abs vdiv" style="left:352px;top:808px;height:172px"></div>

    <h2 class="abs col-heading" style="left:390px">WHY CHOOSE US?</h2>
    <div class="abs col-text" style="left:390px;top:848px;width:200px">
      <div class="list-item"><svg class="tick" width="10" height="9"><polyline points="1,5 4,8 9,1" fill="none" stroke="#888" stroke-width="2"/></svg><span>Lorem ipsum dolor sit amet, consectetur adipisicing elit.</span></div>
      <div class="list-item"><svg class="tick" width="10" height="9"><polyline points="1,5 4,8 9,1" fill="none" stroke="#888" stroke-width="2"/></svg><span>Lorem ipsum dolor sit amet, consectetur adipisicing elit.</span></div>
      <div class="list-item"><svg class="tick" width="10" height="9"><polyline points="1,5 4,8 9,1" fill="none" stroke="#888" stroke-width="2"/></svg><span>Lorem ipsum dolor sit amet, consectetur adipisicing elit.</span></div>
    </div>
    <span class="abs btn btn-dark" style="left:391px;top:962px;height:19px;line-height:19px;padding:0 11px">READ MORE</span>
    <div class="abs vdiv" style="left:610px;top:808px;height:172px"></div>

    <h2 class="abs col-heading" style="left:642px">LATEST NEWS</h2>
    <div class="abs col-text" style="left:642px;top:848px;width:196px">
      <div class="list-item" style="gap:0"><span class="num">01</span><span>Lorem ipsum dolor sit amet, consectetur adipisicing elit.</span></div>
      <div class="list-item" style="gap:0"><span class="num">02</span><span>Lorem ipsum dolor sit amet, consectetur adipisicing elit.</span></div>
      <div class="list-item" style="gap:0"><span class="num">03</span><span>Lorem ipsum dolor sit amet, consectetur adipisicing elit.</span></div>
    </div>
    <span class="abs btn btn-dark" style="left:643px;top:962px;height:19px;line-height:19px;padding:0 11px">VIEW ALL</span>
  </section>

  <footer>
    <div class="abs footer"></div>
    <div class="abs f-head" style="left:130px;top:1041px">NAVIGATION</div>
    <ul class="abs f-links" style="left:130px;top:1057px">
      <li>Home</li><li>About Us</li><li>Products</li><li>Accessories</li><li>Contact Us</li>
    </ul>
    <div class="abs fdiv" style="left:230px"></div>
    <div class="abs f-head" style="left:264px;top:1041px">ORDER ONLINE</div>
    <ul class="abs f-links" style="left:264px;top:1057px">
      <li>Terms &amp; Conditions</li><li>Delivery</li><li>Faq`s</li>
    </ul>
    <div class="abs fdiv" style="left:385px"></div>
    <div class="abs f-head" style="left:428px;top:1041px">PAYMENT OPTION</div>
    <div class="abs card" style="left:428px;top:1060px"></div>
    <div class="abs card" style="left:466px;top:1060px"></div>
    <div class="abs card" style="left:504px;top:1060px"></div>
    <div class="abs f-head" style="left:428px;top:1099px">FOLLOW US ON</div>
    <div class="abs social" style="left:428px;top:1118px;background:#3b5b98"></div>
    <div class="abs social" style="left:454px;top:1118px;background:#2aa3e0"></div>
    <div class="abs social" style="left:480px;top:1118px;background:#1c78b4"></div>
    <div class="abs social" style="left:506px;top:1118px;background:#d9533f"></div>
    <div class="abs fdiv" style="left:570px"></div>
    <div class="abs" style="left:608px;top:1036px;font-size:13px;font-weight:700;color:#fff">Happy Client`s</div>
    <div class="abs" style="left:608px;top:1058px;width:230px;font-size:9px;line-height:11px;color:#fff">Lorem ipsum dolor sit amet, consectetur adipisicing elit, sed do eiusmod tempor incididunt ut labore et dolore magna aliqua.</div>
    <div class="abs" style="left:608px;top:1102px;font-size:9px;color:#fff"><b>Ellis.</b> 15/06/13</div>
    <span class="abs btn btn-light" style="left:609px;top:1128px;height:19px;line-height:17px;padding:0 10px">READ MORE</span>
    <div class="abs copyright">COPYRIGHT © TALL RIDGE FIREWOOD 2013. ALL RIGHT RESERVED.</div>
  </footer>
</div>
</body>
</html>
```